Business Card Design

New business card design

Target Market(s)

Residential & Commercial Property Managers

Industry/Entity Type

Plumbing Services

Contact Information for Business Card

Name - Rowan Keddle, title - Director, Phone Number - 0431 286 517, email - rowan@tbk-plumbing.com.au, Company ABN - 73 215 904 386,

Font styles to use
Sans Serif

Colors
0054AA
0677BA
7BADD7
CADEEF
E8F1F8

```html
<!DOCTYPE html>
<html lang="en">
<head>
<meta charset="utf-8">
<title>TBK Plumbing Services – Business Card</title>
<link href="https://fonts.googleapis.com/css2?family=Poppins:wght@300;400;500;600&family=Exo+2:wght@600&family=Michroma&family=Oswald:wght@300&display=swap" rel="stylesheet">
<style>
  :root {
    --stage: #7a7a7a;
    --card-dark: #22272e;
    --card-dark-light: #2b3139;
    --accent: #00a8e8;
    --accent-deep: #0399d6;
    --white: #ffffff;
    --tagline: #5c5148;
    --icon-dark: #1f242b;
  }
  * { margin: 0; padding: 0; box-sizing: border-box; }
  html, body { width: 921px; height: 1200px; overflow: hidden; }
  body {
    background: var(--stage);
    position: relative;
    font-family: "Poppins", sans-serif;
  }
  .card {
    position: absolute;
    left: 96px;
    width: 729px;
    height: 418px;
    overflow: hidden;
    background: radial-gradient(ellipse at 15% 10%, var(--card-dark-light), var(--card-dark) 60%);
    box-shadow: 0 8px 12px rgba(0,0,0,0.35);
  }
  .card-front {
    top: 145px;
    border-left: 2px solid var(--accent);
    border-bottom: 2px solid var(--accent);
  }
  .card-back {
    top: 630px;
  }
  .card-back .edge {
    position: absolute; left: 0; top: 0; width: 2px; height: 224px;
    background: var(--accent);
  }
  .wordmark {
    position: absolute;
    color: var(--white);
    font-family: "Poppins", sans-serif;
    font-weight: 300;
    line-height: 1;
    text-align: center;
  }
  .card-front .wordmark {
    left: 0; right: 0; top: 88px;
    font-size: 122px;
    letter-spacing: 28px;
    padding-left: 28px;
  }
  .tagline {
    position: absolute;
    font-family: "Oswald", sans-serif;
    font-weight: 300;
    color: var(--tagline);
    text-transform: lowercase;
    white-space: nowrap;
  }
  .card-front .tagline {
    left: 0; right: 0; top: 278px;
    text-align: center;
    font-size: 22px;
    letter-spacing: 22px;
    padding-left: 22px;
  }
  .card-back .wordmark {
    left: 63px; width: 267px; top: 62px;
    font-size: 64px;
    letter-spacing: 16px;
    padding-left: 16px;
  }
  .card-back .tagline {
    left: 63px; width: 267px; top: 148px;
    text-align: center;
    font-size: 12px;
    letter-spacing: 11.4px;
    padding-left: 11px;
  }
  .person-name {
    position: absolute;
    left: 387px; top: 66px;
    font-family: "Exo 2", sans-serif;
    font-weight: 600;
    font-size: 36px;
    color: var(--accent);
    white-space: nowrap;
    letter-spacing: 0.5px;
  }
  .person-title {
    position: absolute;
    left: 388px; top: 107px;
    font-family: "Michroma", sans-serif;
    font-size: 16px;
    letter-spacing: 4px;
    color: var(--white);
  }
  .contact-band {
    position: absolute;
    left: 0; right: 0; top: 224px; bottom: 0;
    background: linear-gradient(180deg, var(--accent) 0%, var(--accent-deep) 100%);
  }
  .contact-line {
    position: absolute;
    left: 58px;
    display: flex;
    align-items: center;
    gap: 11px;
    color: var(--white);
    font-size: 22px;
    font-weight: 400;
    white-space: nowrap;
  }
  .contact-line.phone { top: 30px; }
  .contact-line.email { top: 65px; }
  .contact-icon { width: 20px; height: 20px; flex: none; }
  .abn {
    position: absolute;
    left: 58px; top: 117px;
    display: flex; gap: 5px;
    font-size: 20px; font-weight: 600; line-height: 29px;
  }
  .abn-label {
    background: var(--white); color: var(--icon-dark);
    padding: 0 8px; border-radius: 2px;
  }
  .abn-number {
    background: var(--icon-dark); color: var(--white);
    padding: 0 9px; border-radius: 3px;
  }
</style>
</head>
<body>

  <section class="card card-front">
    <div class="wordmark">tbk</div>
    <div class="tagline">plumbing services</div>
  </section>

  <section class="card card-back">
    <div class="edge"></div>
    <div class="wordmark">tbk</div>
    <div class="tagline">plumbing services</div>
    <div class="person-name">Rowan Keddle</div>
    <div class="person-title">Director</div>

    <div class="contact-band">
      <div class="contact-line phone">
        <svg class="contact-icon" viewBox="0 0 20 20" aria-hidden="true">
          <rect width="20" height="20" rx="3" fill="var(--icon-dark)"/>
          <path d="M6 4.5c.6-.4 1.3-.3 1.6.3l1 1.8c.3.5.1 1.1-.3 1.4l-.7.5c.5 1.3 1.5 2.4 2.8 3l.5-.7c.3-.4.9-.6 1.4-.3l1.8 1c.6.3.7 1 .3 1.6l-.8 1c-.5.6-1.4.8-2.2.5-3-1.2-5.3-3.6-6.4-6.6-.3-.8-.1-1.7.5-2.2z" fill="var(--white)"/>
        </svg>
        <span>0431 286 517</span>
      </div>
      <div class="contact-line email">
        <svg class="contact-icon" viewBox="0 0 20 20" aria-hidden="true">
          <rect width="20" height="20" rx="3" fill="var(--icon-dark)"/>
          <rect x="4" y="6" width="12" height="8.5" rx="1" fill="var(--white)"/>
          <path d="M4.5 6.5 10 10.5l5.5-4" fill="none" stroke="var(--icon-dark)" stroke-width="1.3"/>
        </svg>
        <span>rowan@tbk-plumbing.com.au</span>
      </div>
      <div class="abn">
        <span class="abn-label">ABN</span>
        <span class="abn-number">73 215 904 386</span>
      </div>
    </div>
  </section>

</body>
</html>
```